Looking for a dynamic business card for a pizzeria.

A business card with our food, logo, and space for name, title, email, website, phone. The card should convey quality, unique, amazing. On the front, I envision food photo or photos with the owners names and contact information. On the back, more food with locations, website, facebook, twitter, instagram icons. It should look polished, not cartoonish, or plain.
Target Market(s)
upscale, local food buyers, 30-50 years in age.
Industry/Entity Type
Restaurant
Contact Information for Business Card
Business Name: Bru'nettix, LLC
Website: www.brunettix.com
Back:
2 locations: (can list on the back of card)
1. Harbor Row
4087 Corlan Avenue
Marrow Bay, WA 98341
360-481-5067
2. Linden Heights
7315 Wendmere Road
Marrow Bay, WA 98347
360-293-8840
front:
EDITABLE space for
Business name
Person's Name
title
2nd title
Email address
cell-phone number
Requirements
Must have
- logo
- my food photo or photos (no watermarks showing)
- locations on back
- Person contact information on front
- full bleed

```html
<!DOCTYPE html>
<html lang="en">
<head>
<meta charset="utf-8">
<title>Bru'nettix Business Card</title>
<link href="https://fonts.googleapis.com/css2?family=Jost:wght@400;500&display=swap" rel="stylesheet">
<style>
  :root {
    --page: #e9e6e1;
    --card: #ffffff;
    --accent-red: #c8252c;
    --accent-green: #2f6a2f;
    --ink: #2e2e2e;
    --icon: #4a4a4a;
    --photo-dark: #3b3d40;
    --photo-dough: #d9c1a2;
    --photo-light: #efe6dc;
    --white: #ffffff;
  }
  * { box-sizing: border-box; margin: 0; padding: 0; }
  html, body {
    width: 1200px; height: 843px; overflow: hidden;
    background: var(--page);
    font-family: "Jost", sans-serif;
    color: var(--ink);
  }
  .sheet { position: relative; width: 1200px; height: 843px; }
  .card {
    position: absolute; left: 270px; width: 660px; height: 377px;
    overflow: hidden; box-shadow: 0 4px 14px rgba(0,0,0,0.18);
  }
  .card-front { top: 30px; }
  .card-back { top: 436px; background: var(--card); }

  .food-photo {
    position: absolute; inset: 0;
    background:
      radial-gradient(ellipse 40% 45% at 45% 62%, var(--photo-dough), transparent 70%),
      radial-gradient(ellipse 30% 30% at 78% 45%, #b98a72, transparent 75%),
      linear-gradient(100deg, var(--photo-dark) 0%, #6b6663 35%, var(--photo-light) 55%, #8a7e76 100%);
  }
  .front-brand {
    position: absolute; left: 34px; top: 58px;
    font-size: 32px; font-weight: 400; color: var(--white);
  }

  .name-ribbon {
    position: absolute; left: 70px; top: 0; width: 180px; height: 130px;
  }
  .name-ribbon svg { position: absolute; inset: 0; }
  .name-ribbon .person {
    position: relative; text-align: center; padding-top: 22px; color: var(--white);
  }
  .person-name { font-size: 21px; font-weight: 400; letter-spacing: 0.5px; }
  .person-title { font-size: 15px; margin-top: 2px; }

  .back-brand {
    position: absolute; right: 40px; top: 100px;
    font-size: 44px; font-weight: 400; color: var(--ink);
  }

  .locations {
    position: absolute; left: 24px; top: 150px;
    font-size: 17px; line-height: 1.12; font-style: normal;
  }
  .location + .location { margin-top: 2px; }
  .location-name, .phone-label { color: var(--accent-green); }

  .contact-list {
    position: absolute; left: 262px; top: 258px; list-style: none;
    font-size: 18px; line-height: 1.5;
  }
  .contact-list li { display: flex; align-items: center; gap: 12px; }
  .contact-list svg { width: 16px; height: 16px; fill: var(--icon); flex: none; }
</style>
</head>
<body>
<main class="sheet">

  <section class="card card-front">
    <div class="food-photo" role="img" aria-label="Close-up photo of hands kneading floured pizza dough"></div>
    <p class="front-brand">Bru'nettix</p>
  </section>

  <section class="card card-back">
    <div class="name-ribbon">
      <svg viewBox="0 0 180 130" preserveAspectRatio="none" aria-hidden="true">
        <polygon points="0,0 180,0 180,92 90,130 0,92" fill="var(--accent-red)"/>
      </svg>
      <div class="person">
        <p class="person-name">DANIEL FERRIS</p>
        <p class="person-title">Founder</p>
      </div>
    </div>

    <p class="back-brand">Bru'nettix</p>

    <address class="locations">
      <div class="location">
        <p class="location-name">Harbor Row</p>
        <p>4087 Corlan Avenue</p>
        <p>Marrow Bay, WA 98341</p>
        <p><span class="phone-label">Phone:</span>360-481-5067</p>
      </div>
      <div class="location">
        <p class="location-name">Linden Heights</p>
        <p>7315 Wendmere Road</p>
        <p>Marrow Bay, WA 98347</p>
        <p><span class="phone-label">Phone:</span>360-293-8840</p>
      </div>
    </address>

    <ul class="contact-list">
      <li>
        <svg viewBox="0 0 16 16" aria-hidden="true"><path d="M4 0h8a1 1 0 0 1 1 1v14a1 1 0 0 1-1 1H4a1 1 0 0 1-1-1V1a1 1 0 0 1 1-1zm1 2v10h6V2zm3 11a1 1 0 1 0 0 2 1 1 0 0 0 0-2z"/></svg>
        <span>689 512 7740</span>
      </li>
      <li>
        <svg viewBox="0 0 16 16" aria-hidden="true"><path d="M0 3h16v10H0zm1.5 1.2V12h13V4.2L8 9z"/><path d="M1 3h14L8 8z"/></svg>
        <span>name@brunettix.com</span>
      </li>
      <li>
        <svg viewBox="0 0 16 16" aria-hidden="true"><path d="M8 0a8 8 0 1 0 0 16A8 8 0 0 0 8 0zm0 2a6 6 0 1 1 0 12A6 6 0 0 1 8 2zm-3 3h4l2 2-2 3-1 3-2-3-1-2z"/></svg>
        <span>www.brunettix.com</span>
      </li>
    </ul>
  </section>

</main>
</body>
</html>
```